Provide bookkeeping and accounting services to small and growing businesses

We need website and logo design using the name Dornaby as the logo.
The target audience are small companies and startups who need:
1) Simple bookkeeping services
2) Accounting advice that only someone with many years of senior financial experience as a CPA can provide.

The services are provided by two individuals. each of whom specialize in one of the areas.

We want the website to be clean without a lot of visual distraction but don't know how to make a boring subject interesting. We believe our potential clients, small business owners, need to find what they want quickly and easily without a lot of verbiage or distractions.

We've attached a draft of the homepage and have completed the text on most of the other pages.

Target Market(s)

small and early stage growth companies in San Diego North County

Industry/Entity Type

Accounting

Number of Pages Required

1 page

Font styles to use
Sans Serif

Colors
86cfc6
33b8a4
85cae6

Requirements
Must have
• We need a design for the website homepage that includes the name Dornaby as the logo. Must include a design for the name.
• Must have color in teal or greenish blue.
Nice to have
• White background, clean, clear, uncluttered.
• We would like to use the design in a Theme on a WordPress website. Themes Paper Lantern and Quiet Harbour are appealing to us.
Should not have
• Moving pictures

```html
<!DOCTYPE html>
<html lang="en">
<head>
<meta charset="utf-8">
<title>Dornaby – Accounting and Bookkeeping</title>
<link href="https://fonts.googleapis.com/css2?family=Cinzel:wght@400;600;700&family=Lato:wght@400;700&family=Montserrat:wght@600&display=swap" rel="stylesheet">
<style>
:root{
  --teal:#33b8a4;
  --teal-soft:#86cfc6;
  --sky:#85cae6;
  --ink:#222;
  --body:#333;
  --muted:#777;
  --light:#f3f3f3;
  --line:#d4d4d4;
  --footer:#3b3b3b;
  --footer-deep:#2a2a2a;
  --white:#fff;
}
*{box-sizing:border-box;margin:0;padding:0}
html,body{width:743px;height:1200px;overflow:hidden}
body{position:relative;background:var(--white);font-family:"Lato",sans-serif;color:var(--body)}
.abs{position:absolute}
.top-rule{left:0;top:0;width:743px;height:2px;background:var(--teal)}
.social{display:flex;gap:6px}
.social span{width:17px;height:17px;border-radius:50%;background:var(--teal);box-shadow:0 1px 2px rgba(0,0,0,.3)}
.social.header{left:50px;top:10px}
.social.header span:nth-child(1){background:#3b5a9a}
.social.header span:nth-child(2){background:#2a7ab8}
.social.header span:nth-child(3){background:#2aa8e0}
.social.header span:nth-child(4){background:#d34836}
.brand{left:271px;top:6px;width:200px;text-align:center}
.brand-name{font-family:"Cinzel",serif;font-weight:400;font-size:33px;color:var(--teal);line-height:38px;letter-spacing:1px}
.brand-tag{border-top:1px solid var(--ink);border-bottom:1px solid var(--teal);margin:2px 12px 0;padding:2px 0 3px;font-family:"Cinzel",serif;font-size:11px;color:var(--ink)}
.phone{left:604px;top:8px;display:flex;align-items:center;gap:5px;font-weight:700;font-size:12px;color:var(--ink)}
.hero{left:0;top:92px;width:743px;height:370px;display:flex}
.hero div{height:100%}
.hero .p1{width:262px;background:linear-gradient(150deg,#8796a8,#c3ccd6 55%,#8b98a8)}
.hero .p2{width:223px;background:linear-gradient(160deg,#3f6fa6,#6f9ccd 50%,#3d6796)}
.hero .p3{width:258px;background:linear-gradient(150deg,#8f6e5c,#b79a88 45%,#7c86a6)}
.hero-title{left:74px;top:230px;width:600px;font-family:"Montserrat",sans-serif;font-weight:600;font-size:15.5px;line-height:22px;color:var(--white);text-shadow:0 1px 3px rgba(0,0,0,.6)}
.nav{left:130px;top:77px;width:493px;height:31px;background:var(--white);display:flex;align-items:center;box-shadow:0 2px 5px rgba(0,0,0,.15);border-radius:4px 4px 0 0}
.nav a{font-family:"Cinzel",serif;font-size:11px;color:var(--ink);text-decoration:none;padding:0 11px;line-height:12px;border-left:1px solid var(--line)}
.nav a.home{background:var(--teal);color:var(--white);height:31px;width:64px;line-height:31px;text-align:center;border:0;border-radius:3px 3px 0 0;margin-right:0}
.nav a.after{border-left:0}
.arrow{top:480px}
.card{top:397px;width:165px}
.card .frame{height:153px;background:var(--teal);padding:9px 9px 10px;box-shadow:0 4px 6px rgba(0,0,0,.15)}
.card .photo{width:100%;height:100%}
.card h3{font-family:"Cinzel",serif;font-weight:600;font-size:12.5px;color:var(--ink);margin:16px 0 0 8px;letter-spacing:.5px}
.card p{font-size:8.6px;line-height:12.5px;margin:8px 0 0 8px;color:var(--body)}
.more{color:var(--teal)}
.welcome{left:0;top:630px;width:743px;height:158px;background:linear-gradient(#f7f7f7,#eeeeee)}
.section-title{font-family:"Cinzel",serif;font-weight:600;color:var(--ink);letter-spacing:.5px}
.section-title em{font-style:normal;color:var(--teal)}
.welcome .section-title{position:absolute;left:0;top:20px;width:743px;text-align:center;font-size:16.5px}
.rule{height:1px;background:var(--line);position:absolute}
.rule::after{content:"";position:absolute;left:var(--accent-left,0);top:-1px;width:var(--accent-w,70px);height:2px;background:var(--teal)}
.welcome p{position:absolute;left:172px;top:56px;width:400px;text-align:center;font-size:9.2px;line-height:13px;color:var(--ink)}
.btn{position:absolute;background:var(--teal);color:var(--white);font-weight:700;font-size:9px;text-align:center;border:1px solid #248f7f;border-radius:2px}
.resources{left:0;top:788px;width:467px;height:233px;background:linear-gradient(120deg,#e1e4e4,#f1f2f2 45%,#e4e6e6)}
.inquiry{left:467px;top:788px;width:276px;height:233px;background:#f4f5f5;box-shadow:-3px 0 6px rgba(0,0,0,.08)}
.resources .section-title,.inquiry .section-title{position:absolute;font-size:15px}
.lead{position:absolute;left:50px;top:57px;font-weight:700;font-size:9.8px;color:var(--ink)}
.ticks{position:absolute;left:50px;top:78px;width:370px;list-style:none}
.ticks li{display:flex;gap:8px;font-size:8.6px;line-height:11.5px;color:var(--ink);margin-bottom:11px}
.ticks svg{flex:none;margin-top:1px}
.field{position:absolute;left:58px;width:168px;height:15px;background:var(--white);border:1px solid #c9c9c9;font-size:8px;color:#555;padding:2px 4px}
.footer{left:0;top:1021px;width:743px;height:149px;background:var(--footer)}
.footer h4{position:absolute;top:20px;font-family:"Cinzel",serif;font-weight:600;font-size:11.5px;color:var(--white);letter-spacing:.5px}
.footer .rule{background:#5a5a5a}
.links{position:absolute;left:50px;top:53px;list-style:none}
.links li{font-size:8.6px;line-height:14.2px;color:var(--white);display:flex;align-items:center;gap:7px}
.links li::before{content:"";border-left:3px solid var(--teal);border-top:2.5px solid transparent;border-bottom:2.5px solid transparent}
.links li.on{color:var(--teal)}
.contact{position:absolute;left:174px;top:55px;width:180px;color:var(--white);font-size:8.6px;line-height:11px}
.contact .row{display:flex;gap:8px}
.contact b{font-weight:700}
.map{position:absolute;left:386px;top:54px;width:133px;height:79px;border:2px solid #bdbdbd;background:linear-gradient(135deg,#cfe3f0,#e7e3d6 50%,#d9d2be)}
.ghost{position:absolute;left:558px;top:62px;width:134px;text-align:center;color:rgba(255,255,255,.22)}
.ghost .n{font-family:"Cinzel",serif;font-size:26px;line-height:30px}
.ghost .t{border-top:1px solid rgba(255,255,255,.22);font-family:"Cinzel",serif;font-size:8.5px;padding-top:3px;margin-top:2px}
.bottom{left:0;top:1170px;width:743px;height:30px;background:var(--footer-deep)}
.bottom p{position:absolute;left:50px;top:9px;font-size:8.6px;color:var(--white)}
.social.foot{position:absolute;left:604px;top:5px}
.social.foot span{width:18px;height:18px;border:1.5px solid var(--white)}
.social.foot span:nth-child(1){background:#3b5a9a}
.social.foot span:nth-child(2){background:#2a7ab8}
.social.foot span:nth-child(3){background:#2aa8e0}
.social.foot span:nth-child(4){background:#d34836}
</style>
</head>
<body>
<div class="abs top-rule"></div>

<header>
  <div class="abs social header" aria-label="Social links"><span></span><span></span><span></span><span></span></div>
  <div class="abs brand">
    <div class="brand-name">Dornaby</div>
    <div class="brand-tag">Accounting and Bookkeeping</div>
  </div>
  <div class="abs phone">
    <svg width="11" height="12" viewBox="0 0 24 24"><path fill="#33b8a4" d="M6.6 10.8a15 15 0 0 0 6.6 6.6l2.2-2.2a1 1 0 0 1 1-.3 11.4 11.4 0 0 0 3.6.6 1 1 0 0 1 1 1V20a1 1 0 0 1-1 1A17 17 0 0 1 3 4a1 1 0 0 1 1-1h3.5a1 1 0 0 1 1 1c0 1.3.2 2.5.6 3.6a1 1 0 0 1-.3 1z"/></svg>
    012-555-0148
  </div>
</header>

<section class="abs hero">
  <div class="p1" role="img" aria-label="Photo of a calculator keypad and printed figures"></div>
  <div class="p2" role="img" aria-label="Photo of a large percent symbol in blue tones"></div>
  <div class="p3" role="img" aria-label="Photo of a business handshake over a spreadsheet"></div>
</section>
<h1 class="abs hero-title">Dornaby Offers A Flexible Range of Accounting And Bookkeeping Services &amp; Support For Small &amp; Growing Organizations in San Diego North County.</h1>

<nav class="abs nav">
  <a class="home">Home</a>
  <a class="after">About Us</a>
  <a>Services</a>
  <a>Experience</a>
  <a>Resources</a>
  <a>Contact Us</a>
</nav>

<svg class="abs arrow" style="left:54px" width="10" height="18" viewBox="0 0 10 18"><path d="M8 2 2 9l6 7" fill="none" stroke="#86cfc6" stroke-width="1.6"/></svg>
<svg class="abs arrow" style="left:679px" width="10" height="18" viewBox="0 0 10 18"><path d="M2 2l6 7-6 7" fill="none" stroke="#33b8a4" stroke-width="1.6"/></svg>

<article class="abs card" style="left:97px">
  <div class="frame"><div class="photo" role="img" aria-label="Photo of two colleagues reviewing documents at a laptop" style="background:linear-gradient(160deg,#f2f4f6,#c9d2da)"></div></div>
  <h3>Bookkeeping</h3>
  <p>Lorem ipsum dolor sit amet, adipiscing consectetuer adipiscing aed <span class="more">[...]</span></p>
</article>
<article class="abs card" style="left:290px">
  <div class="frame"><div class="photo" role="img" aria-label="Photo of charts, a calculator and pens on a desk" style="background:linear-gradient(150deg,#dfe6ef,#8fb0d6 55%,#4c4f58)"></div></div>
  <h3>Controller Services</h3>
  <p>Lorem ipsum dolor sit amet, adipiscing consectetuer adipiscing aed <span class="more">[...]</span></p>
</article>
<article class="abs card" style="left:484px">
  <div class="frame"><div class="photo" role="img" aria-label="Photo of a payroll form with a pen" style="background:linear-gradient(160deg,#d5d8db,#eef0f2 50%,#b9c1cc)"></div></div>
  <h3 style="margin-top:15px">Payroll</h3>
  <p>Lorem ipsum dolor sit amet, adipiscing consectetuer adipiscing aed <span class="more">[...]</span></p>
</article>

<section class="abs welcome">
  <h2 class="section-title">Welcome To <em>Dornaby</em> Accounting and Bookkeeping</h2>
  <div class="rule" style="left:128px;top:48px;width:487px;--accent-left:208px;--accent-w:70px"></div>
  <p>Dornaby offers a flexible range of accounting and bookkeeping services and support for small and growing organizations in San Diego North County. We provide bookkeeping services specializing in LedgerPro at your offices or remotely from ours. We also provide a broad range of accounting services or financial advice.</p>
  <div class="btn" style="left:345px;top:124px;width:53px;height:17px;line-height:15px">Read More</div>
</section>

<section class="abs resources">
  <h2 class="section-title" style="left:50px;top:26px">Our Resources</h2>
  <div class="rule" style="left:50px;top:45px;width:190px;--accent-w:72px"></div>
  <p class="lead">Lorem ipsum dolor sit amet, consectetuer adipiscing elit</p>
  <ul class="ticks">
    <li><svg width="10" height="10" viewBox="0 0 10 10"><rect x=".5" y="1.5" width="8" height="8" fill="none" stroke="#33b8a4"/><path d="M2 5l2 2 5-6" fill="none" stroke="#33b8a4" stroke-width="1.3"/></svg>Lorem ipsum dolor sit amet, consectetuer adipiscing elit, sed diam nonummy nibh euismod tincidunt ut laoreet dolore magna aliquam erat volutpat. Ut wisi enim ad minim veniam.</li>
    <li><svg width="10" height="10" viewBox="0 0 10 10"><rect x=".5" y="1.5" width="8" height="8" fill="none" stroke="#33b8a4"/><path d="M2 5l2 2 5-6" fill="none" stroke="#33b8a4" stroke-width="1.3"/></svg>Lorem ipsum dolor sit amet, consectetuer adipiscing elit, sed diam nonummy nibh euismod tincidunt ut laoreet dolore magna aliquam erat volutpat. Ut wisi enim ad minim veniam.</li>
    <li><svg width="10" height="10" viewBox="0 0 10 10"><rect x=".5" y="1.5" width="8" height="8" fill="none" stroke="#33b8a4"/><path d="M2 5l2 2 5-6" fill="none" stroke="#33b8a4" stroke-width="1.3"/></svg>Lorem ipsum dolor sit amet, consectetuer adipiscing elit, sed diam nonummy nibh euismod tincidunt ut laoreet dolore magna aliquam erat volutpat. Ut wisi enim ad minim veniam.</li>
  </ul>
  <div class="btn" style="left:50px;top:186px;width:53px;height:17px;line-height:15px">Read More</div>
</section>

<section class="abs inquiry">
  <h2 class="section-title" style="left:58px;top:26px">Quick <em>Inquiry</em></h2>
  <div class="rule" style="left:58px;top:46px;width:168px;--accent-w:73px"></div>
  <div class="field" style="top:64px">Name:</div>
  <div class="field" style="top:89px">Company:</div>
  <div class="field" style="top:113px">Subject :</div>
  <div class="field" style="top:140px;height:28px">Message :</div>
  <div class="btn" style="left:58px;top:186px;width:53px;height:17px;line-height:15px;font-size:10px">Submit</div>
</section>

<footer class="abs footer">
  <h4 style="left:50px">Quick Links</h4>
  <div class="rule" style="left:50px;top:41px;width:84px;--accent-w:43px"></div>
  <ul class="links">
    <li class="on">Home</li><li>About Us</li><li>Services</li><li>Experience</li><li>Resources</li><li>Contact Us</li>
  </ul>

  <h4 style="left:174px">Contact Information</h4>
  <div class="rule" style="left:174px;top:41px;width:146px;--accent-w:46px"></div>
  <div class="contact">
    <div class="row"><svg width="7" height="10" viewBox="0 0 14 20"><path fill="#33b8a4" d="M7 0a7 7 0 0 0-7 7c0 5 7 13 7 13s7-8 7-13a7 7 0 0 0-7-7zm0 10a3 3 0 1 1 0-6 3 3 0 0 1 0 6z"/></svg><div><b>Dornaby Accounting and Bookkeeping</b><br>42 Harbor Lane Suite 12, Coral Bay,<br>CA 92011</div></div>
    <div class="row" style="margin-top:13px;font-size:10px;font-weight:700"><svg width="10" height="10" viewBox="0 0 24 24"><path fill="#33b8a4" d="M6.6 10.8a15 15 0 0 0 6.6 6.6l2.2-2.2a1 1 0 0 1 1-.3 11.4 11.4 0 0 0 3.6.6 1 1 0 0 1 1 1V20a1 1 0 0 1-1 1A17 17 0 0 1 3 4a1 1 0 0 1 1-1h3.5a1 1 0 0 1 1 1c0 1.3.2 2.5.6 3.6a1 1 0 0 1-.3 1z"/></svg>012-555-0148</div>
    <div class="row" style="margin-top:13px"><svg width="10" height="8" viewBox="0 0 20 14"><rect width="20" height="14" fill="#33b8a4"/><path d="M0 0l10 8 10-8" fill="none" stroke="#3b3b3b" stroke-width="1.5"/></svg>info@dornaby.com</div>
  </div>

  <h4 style="left:387px">Location Map</h4>
  <div class="rule" style="left:387px;top:41px;width:132px;--accent-w:45px"></div>
  <div class="map" role="img" aria-label="Map of the office location"></div>

  <div class="ghost">
    <div class="n">Dornaby</div>
    <div class="t">Accounting and Bookkeeping</div>
  </div>
</footer>

<div class="abs bottom">
  <p>Copyright © 2016 Dornaby Accounting and Bookkeeping. All Right Reserved</p>
  <div class="social foot" aria-label="Social links"><span></span><span></span><span></span><span></span></div>
</div>
</body>
</html>
```